Constant Contact email marketing template

I need engaging customizable templates that can be used in multiple fundraising campaigns.

I included a school bus project that we used in a previous campaign. This campaign, however, is a $25 for $25 promotion. Consumers make a $25 contribution for the school or charity and receive back a $25 e-gift card to be used at area restaurants.

Important! This is a completely generic piece, capable of being used in schools, churches, or other civic organizations.

The 5 part example is NOT what I am looking for. I included it to suggest the concept. I am looking forward to viewing YOUR designs,

Target Market(s)

schools, leagues, nonprofit organizations

Font styles to use
Sans Serif

Colors

Designer to choose colors to be used in the design.

Requirements
Must have
• Must clearly present itself as a fundraising tool for schools, leagues and Nonprofit organizations.
• Must have 2 clickable buttons that allow member to click

```html
<!DOCTYPE html>
<html lang="en">
<head>
<meta charset="utf-8">
<title>$25 for $25 Fundraiser</title>
<link href="https://fonts.googleapis.com/css2?family=Open+Sans:wght@400;700&family=Oswald:wght@300;400&family=Roboto+Condensed:wght@400&family=Kaushan+Script&display=swap" rel="stylesheet">
<style>
  :root {
    --black: #000000;
    --brand-red: #9b1c1f;
    --sky: #22a3da;
    --sky-light: #3bb6e8;
    --gold: #f2c12e;
    --yellow-text: #fbe94a;
    --sign-red: #d8385a;
    --sign-dark: #a81c3f;
    --button-red: #e3401f;
    --button-orange: #e7a42a;
    --heading-blue: #7bbde0;
    --ink: #222222;
    --grey: #666666;
    --white: #ffffff;
  }
  * { margin: 0; padding: 0; box-sizing: border-box; }
  html, body { width: 1200px; height: 2452px; overflow: hidden; background: var(--white); }
  .email { position: relative; width: 1200px; height: 2452px; font-family: "Open Sans", sans-serif; }

  .masthead { position: absolute; left: 0; top: 0; width: 1200px; height: 262px; background: var(--black); }
  .org-badge {
    position: absolute; left: 46px; top: 46px; width: 441px; height: 178px;
    background: var(--brand-red); display: flex; align-items: center; justify-content: center; gap: 18px;
  }
  .org-badge .dot { width: 26px; height: 26px; border-radius: 50%; background: var(--white); }
  .org-badge .name { font-weight: 700; color: var(--white); font-size: 34px; line-height: 1.1; }
  .campaign-title { position: absolute; left: 505px; top: 0; width: 680px; height: 262px; }
  .campaign-title .rule { position: absolute; left: 35px; top: 70px; width: 326px; height: 4px; background: var(--white); }
  .campaign-title .greatest { position: absolute; right: 70px; top: 4px; font-family: "Kaushan Script", cursive; color: var(--white); font-size: 58px; line-height: 1; }
  .campaign-title .fundraiser { position: absolute; right: 12px; top: 92px; font-family: "Oswald", sans-serif; font-weight: 400; color: var(--gold); font-size: 54px; line-height: 1; letter-spacing: 26px; }
  .campaign-title .ever { position: absolute; right: 18px; top: 140px; font-family: "Kaushan Script", cursive; color: var(--white); font-size: 96px; line-height: 1; }

  .hero { position: absolute; left: 0; top: 262px; width: 1200px; height: 1443px; background: linear-gradient(180deg, var(--sky) 0%, var(--sky-light) 60%, var(--sky) 100%); }
  .sign-art {
    position: absolute; left: 90px; top: 10px; width: 1030px; height: 580px; border-radius: 24px;
    background: linear-gradient(160deg, #e3567a 0%, var(--sign-red) 50%, var(--sign-dark) 100%);
  }

  .headline { position: absolute; left: 0; top: 600px; width: 1200px; text-align: center; color: var(--white); font-weight: 700; font-size: 52px; line-height: 62px; }
  .subline { position: absolute; left: 0; top: 818px; width: 1200px; text-align: center; color: var(--white); font-size: 22px; letter-spacing: 1.5px; line-height: 26px; }
  .benefits { position: absolute; left: 170px; top: 888px; list-style: none; }
  .benefits li { display: flex; align-items: center; gap: 18px; height: 52px; color: var(--yellow-text); font-weight: 700; font-size: 32px; }
  .benefits svg { width: 36px; height: 36px; }

  .btn {
    position: absolute; left: 180px; width: 820px; display: flex; align-items: center; justify-content: center;
    text-decoration: none; font-family: "Oswald", sans-serif; font-weight: 300; color: var(--white); text-transform: uppercase;
    border: 8px solid #e6e6e6; border-radius: 46px; box-shadow: 0 6px 12px rgba(0,0,0,.25);
  }
  .btn-donate { top: 1098px; height: 186px; font-size: 76px; background: linear-gradient(180deg, #f2572b 0%, var(--button-red) 55%, #b8200f 100%); }
  .btn-behalf { top: 1348px; height: 188px; font-size: 40px; color: #3a2a10; background: linear-gradient(180deg, #f0c13a 0%, var(--button-orange) 60%, #c97c1c 100%); }

  .offer { position: absolute; left: 0; top: 1785px; width: 1200px; text-align: center; color: var(--heading-blue); font-weight: 700; font-size: 76px; line-height: 100px; }
  .offer-copy { position: absolute; left: 163px; top: 1893px; width: 840px; font-family: "Roboto Condensed", sans-serif; font-size: 22px; line-height: 39px; color: var(--ink); text-align: justify; }
  .contact { position: absolute; left: 0; top: 2138px; width: 1200px; display: flex; justify-content: center; align-items: center; gap: 22px; color: var(--grey); font-size: 29px; }
  .social { display: flex; gap: 10px; }
  .social span { width: 30px; height: 30px; border-radius: 50%; }
  .divider { position: absolute; left: 30px; top: 2199px; width: 1130px; height: 2px; background: #bbbbbb; }
  .footer { position: absolute; left: 0; top: 2264px; width: 1200px; text-align: center; font-family: "Roboto Condensed", sans-serif; font-size: 15px; letter-spacing: 7px; color: var(--ink); line-height: 21px; }
  .footer .gap { height: 26px; }
</style>
</head>
<body>
<div class="email">
  <header class="masthead">
    <div class="org-badge"><span class="dot"></span><span class="name">Brookfield<br>Community Schools</span></div>
    <div class="campaign-title">
      <div class="rule"></div>
      <div class="greatest">greatest</div>
      <div class="fundraiser">FUNDRAISER</div>
      <div class="ever">ever!</div>
    </div>
  </header>

  <section class="hero">
    <div class="sign-art" role="img" aria-label="Illustration: marquee light-bulb arrow signs reading 'Contribute $25' and 'you get a $25 e-gift card' inside an orange frame"></div>

    <h1 class="headline">Simply donate $25 and we give<br>you $25 back in e-Gift Cards for<br>restaurants in your area!</h1>
    <p class="subline">"SED UT PERSPICIATIS UNDE OMNIS ISTE NATUS ERROR SIT<br>VOLUPTATEM AC</p>
    <ul class="benefits">
      <li><svg viewBox="0 0 34 34"><path d="M2,16 L13,30 L32,2 L13,22 Z" fill="#e2231a"/></svg>More than 500,000 deals available every day</li>
      <li><svg viewBox="0 0 34 34"><path d="M2,16 L13,30 L32,2 L13,22 Z" fill="#e2231a"/></svg>Local independent neighborhood restaurants</li>
      <li><svg viewBox="0 0 34 34"><path d="M2,16 L13,30 L32,2 L13,22 Z" fill="#e2231a"/></svg>Always available. Never expire.</li>
    </ul>

    <a class="btn btn-donate" href="#">Donate now!</a>
    <a class="btn btn-behalf" href="#">Donate on behalf of a loved one or friend</a>
  </section>

  <h2 class="offer">$25 for $25</h2>
  <p class="offer-copy">"Sed ut perspiciatis unde omnis iste natus error sit voluptatem accusantium doloremque laudantium, totam rem aperiam, eaque ipsa quae ab illo inventore veritatis et quasi architecto beatae vitae dicta sunt explicabo. Nemo enim ipsam voluptatem quia voluptas sit aspernatur aut odit aut fugit, sed quia consequuntur magni dolores eos qui ratione voluptatem sequi nesciunt.</p>

  <div class="contact">
    <span>www.<b>website</b>.com.br</span>
    <span class="social"><span style="background:#3b5998"></span><span style="background:#7a5b4a"></span><span style="background:#cb2027"></span></span>
    <span>Phone 12345687 - email@email.com</span>
  </div>
  <div class="divider"></div>

  <footer class="footer">
    <div>TEXT INC - ADRESS HERE NUMBER 1234 - 012346</div>
    <div class="gap"></div>
    <div>UNSUBSCRIBE - HERE</div>
    <div>UPDATE PROFILE - ABOUT OUR SERVICE PROVIDER</div>
    <div>SENT BY SUPPORT@TABLEGIVE.ORG IN COLLABORATION WITH</div>
  </footer>
</div>
</body>
</html>
```